Moravel Aesthetic Doctor

I require an elegant, luxurious looking business card for my aesthetic business. I am a doctor and that will set me aside from competitors. I am planning to provide home and spa based treatments to clients with high expectations. I have attached my logo.

```html
<!DOCTYPE html>
<html lang="en">
<head>
<meta charset="utf-8">
<title>Moravel Aesthetic Doctor – Business Card</title>
<link rel="stylesheet" href="https://fonts.googleapis.com/css2?family=Marcellus&family=Montserrat:wght@400;500&display=swap">
<style>
  :root {
    --backdrop: #dcdde1;
    --brand-deep: #1b5b8e;
    --brand-mid: #2f80b3;
    --brand-accent: #2a7fc1;
    --sky-light: #a9d8ef;
    --sky-mid: #5fb3e2;
    --paper: #f8f8f9;
    --paper-shade: #e8e8ea;
    --ink: #3d3f44;
    --ink-soft: #6a6d73;
    --white: #ffffff;
  }
  * { box-sizing: border-box; margin: 0; padding: 0; }
  html, body {
    width: 1200px;
    height: 800px;
    overflow: hidden;
    background: var(--backdrop);
  }
  .canvas {
    position: relative;
    width: 1200px;
    height: 800px;
  }
  .card {
    position: absolute;
    left: 320px;
    width: 560px;
    height: 320px;
    overflow: hidden;
  }
  .card--front {
    top: 55px;
    background: linear-gradient(200deg, var(--brand-mid) 0%, #2672a8 45%, var(--brand-deep) 100%);
  }
  .card--back {
    top: 425px;
    background: radial-gradient(ellipse at 75% 40%, var(--white) 0%, var(--paper) 45%, var(--paper-shade) 100%);
  }

  /* Front */
  .brand-mark {
    position: absolute;
    left: 128px;
    top: 110px;
    width: 72px;
    height: 72px;
    border-radius: 50%;
    background: var(--sky-light);
  }
  .brand-name {
    position: absolute;
    left: 216px;
    top: 104px;
    color: var(--white);
    font-family: "Marcellus", serif;
    font-weight: 400;
    text-transform: uppercase;
    line-height: 1;
  }
  .brand-name__main {
    display: block;
    font-size: 50px;
    letter-spacing: 3px;
  }
  .brand-name__sub {
    display: block;
    margin-top: 8px;
    font-size: 20px;
    letter-spacing: 2.4px;
  }
  .tagline {
    position: absolute;
    left: 0;
    right: 0;
    top: 274px;
    text-align: center;
    color: #e6f1f8;
    font-family: "Montserrat", sans-serif;
    font-size: 17px;
    letter-spacing: 0.3px;
  }

  /* Back */
  .practitioner {
    position: absolute;
    left: 30px;
    top: 28px;
    font-family: "Montserrat", sans-serif;
  }
  .practitioner__name {
    color: var(--brand-accent);
    font-size: 16.5px;
    font-weight: 500;
  }
  .practitioner__post {
    color: var(--ink-soft);
    font-size: 9px;
    font-weight: 500;
    margin-left: 3px;
  }
  .practitioner__credential {
    margin-top: 4px;
    color: var(--ink);
    font-size: 14px;
    line-height: 16px;
  }
  .contact-list {
    position: absolute;
    left: 30px;
    top: 234px;
    list-style: none;
    font-family: "Montserrat", sans-serif;
    font-size: 13.5px;
    color: var(--ink);
  }
  .contact-list__item {
    display: flex;
    align-items: center;
    height: 17px;
  }
  .contact-list__icon {
    width: 10px;
    height: 10px;
    margin-right: 8px;
    fill: var(--brand-accent);
  }
  .symbol-area {
    position: absolute;
    left: 236px;
    top: 30px;
    width: 270px;
    height: 270px;
    border-radius: 50%;
    background: radial-gradient(circle at 60% 45%, var(--sky-mid) 0%, var(--sky-light) 65%, #cfe9f6 100%);
  }
</style>
</head>
<body>
<main class="canvas">

  <section class="card card--front" aria-label="Card front">
    <span class="brand-mark" aria-hidden="true"></span>
    <h1 class="brand-name">
      <span class="brand-name__main">Moravel</span>
      <span class="brand-name__sub">Aesthetic Doctor</span>
    </h1>
    <p class="tagline">Home and Spa Based Treatments</p>
  </section>

  <section class="card card--back" aria-label="Card back">
    <div class="practitioner">
      <p><span class="practitioner__name">Dr Elsa Varn</span><span class="practitioner__post">MRCPCH MD</span></p>
      <p class="practitioner__credential">Australasian Diploma<br>of Aesthetic Medicine</p>
    </div>

    <ul class="contact-list">
      <li class="contact-list__item">
        <svg class="contact-list__icon" viewBox="0 0 10 10" aria-hidden="true"><path d="M2 0.5 L3.6 0.5 L4.2 2.8 L3 3.6 Q3.8 5.6 6 6.9 L6.8 5.8 L9.5 6.4 L9.5 8 Q9.5 9.5 8 9.5 Q1 8.6 0.5 2 Q0.5 0.5 2 0.5 Z"/></svg>
        0800 555 014
      </li>
      <li class="contact-list__item">
        <svg class="contact-list__icon" viewBox="0 0 10 10" aria-hidden="true"><path d="M0 2 H10 V8.5 H0 Z M0.6 2.4 L5 5.6 L9.4 2.4" fill="var(--brand-accent)" stroke="var(--paper)" stroke-width="0.8"/></svg>
        elsa@moravel.co.nz
      </li>
      <li class="contact-list__item">
        <svg class="contact-list__icon" viewBox="0 0 10 10" aria-hidden="true"><circle cx="5" cy="5" r="4.5" fill="none" stroke="var(--brand-accent)" stroke-width="0.9"/><ellipse cx="5" cy="5" rx="2" ry="4.5" fill="none" stroke="var(--brand-accent)" stroke-width="0.8"/><path d="M0.5 5 H9.5 M1.3 2.8 H8.7 M1.3 7.2 H8.7" stroke="var(--brand-accent)" stroke-width="0.7"/></svg>
        www.moravel.co.nz
      </li>
    </ul>

    <div class="symbol-area" role="img" aria-label="Large brand symbol in layered light blue tones"></div>
  </section>

</main>
</body>
</html>
```